Business Card Design for Training Business

Clear Path Coaching is a new business that delivers training and other services with a focus on topics related to mental health and wellbeing, for example, Wellmind Response Course, Resilience etc. We have a strong focus on evidence-based psychology and neuroscience. I have a logo which I will upload with the brief, so please consider colours that work well with the logo.
Target Market(s)
Adults, workplaces (particularly government and not-for-profits)
Industry/Entity Type
Business
Contact Information for Business Card
Head Strong TrainingSamantha SellwoodDirector0438 770 850sam@headstrongtraining.com.auwww.headstrongtraining.com.au

```html
<!DOCTYPE html>
<html lang="en">
<head>
<meta charset="utf-8">
<title>Clear Path Coaching – Business Card</title>
<link rel="stylesheet" href="https://fonts.googleapis.com/css2?family=Josefin+Sans:wght@300&family=Arimo:wght@400;700&display=swap">
<style>
  :root {
    --page-bg: #dcdcdc;
    --card-light: #f4f5f5;
    --card-light-edge: #e9ebeb;
    --card-grey: #bcbcbc;
    --band-teal: #6fcac9;
    --band-gap: #f7f7f7;
    --brand-ink: #7d716c;
    --text-ink: #151515;
  }
  * { box-sizing: border-box; margin: 0; padding: 0; }
  html, body { width: 1200px; height: 864px; overflow: hidden; }
  body {
    background: var(--page-bg);
    font-family: "Arimo", Arial, sans-serif;
    position: relative;
  }
  .business-card {
    position: absolute;
    left: 100px; top: 146px;
    width: 1000px; height: 572px;
    background: var(--card-light);
    overflow: hidden;
    box-shadow: 0 6px 24px rgba(0,0,0,0.18);
  }
  .texture-area {
    position: absolute; inset: 0;
    background: radial-gradient(ellipse at 65% 30%, var(--card-light) 0%, var(--card-light-edge) 70%);
  }
  .card-shapes { position: absolute; inset: 0; }
  .brand {
    position: absolute;
    left: 130px; top: 40px;
    display: flex; align-items: center; gap: 90px;
  }
  .brand-mark {
    width: 190px; height: 190px;
    border: 3px solid var(--band-teal);
    border-radius: 50%;
  }
  .brand-name {
    font-family: "Josefin Sans", sans-serif;
    font-weight: 300;
    color: var(--brand-ink);
    font-size: 44px;
    letter-spacing: 6px;
    line-height: 1.15;
    text-transform: uppercase;
    margin-top: 60px;
  }
  .holder {
    position: absolute;
    right: 590px; top: 320px;
    text-align: right;
    color: var(--text-ink);
  }
  .holder-name { font-weight: 700; font-size: 30px; }
  .holder-role { font-weight: 700; font-size: 21px; margin-top: 4px; }
  .divider {
    position: absolute;
    left: 440px; top: 312px;
    width: 2px; height: 186px;
    background: var(--text-ink);
  }
  .contact-list {
    position: absolute;
    left: 470px; top: 330px;
    list-style: none;
    color: var(--text-ink);
    font-size: 26px;
  }
  .contact-list li {
    display: flex; align-items: center; gap: 16px;
    height: 40px;
  }
  .contact-icon { width: 20px; height: 20px; flex: none; }
</style>
</head>
<body>
  <section class="business-card">
    <div class="texture-area" role="img" aria-label="Faint light grey pattern texture across the card background"></div>

    <svg class="card-shapes" viewBox="0 0 1000 572" width="1000" height="572" aria-hidden="true">
      <path fill="var(--band-teal)" d="M0,192 C260,215 450,300 650,322 C820,340 930,400 1000,470 L1000,572 L0,572 Z"/>
      <path fill="var(--band-gap)" d="M0,208 C260,232 450,318 650,340 C820,358 930,418 1000,488 L1000,572 L0,572 Z"/>
      <path fill="var(--card-grey)" d="M0,214 C260,238 450,324 650,346 C820,364 930,424 1000,494 L1000,572 L0,572 Z"/>
    </svg>

    <div class="brand">
      <div class="brand-mark"></div>
      <div class="brand-name">Clear Path<br>Coaching</div>
    </div>

    <div class="holder">
      <p class="holder-name">Rebecca Tanfield</p>
      <p class="holder-role">Director</p>
    </div>

    <div class="divider"></div>

    <ul class="contact-list">
      <li>
        <svg class="contact-icon" viewBox="0 0 20 20" aria-hidden="true">
          <rect width="20" height="20" fill="#151515"/>
          <path d="M6 4 L8.5 4 L9.5 7 L8 8.2 C8.8 10 10 11.2 11.8 12 L13 10.5 L16 11.5 L16 14 C11 15 5 9 6 4 Z" fill="#fff"/>
        </svg>
        <span>0491 362 517</span>
      </li>
      <li>
        <svg class="contact-icon" viewBox="0 0 20 20" aria-hidden="true">
          <rect width="20" height="20" fill="#151515"/>
          <rect x="4" y="6" width="12" height="8" fill="none" stroke="#fff" stroke-width="1.4"/>
          <path d="M4 6 L10 11 L16 6" fill="none" stroke="#fff" stroke-width="1.4"/>
        </svg>
        <span>bec@clearpathcoaching.example.au</span>
      </li>
      <li>
        <svg class="contact-icon" viewBox="0 0 20 20" aria-hidden="true">
          <rect width="20" height="20" fill="#151515"/>
          <circle cx="10" cy="10" r="5.5" fill="none" stroke="#fff" stroke-width="1.4"/>
          <path d="M4.5 10 H15.5 M10 4.5 C7 7.5 7 12.5 10 15.5 M10 4.5 C13 7.5 13 12.5 10 15.5" fill="none" stroke="#fff" stroke-width="1.2"/>
        </svg>
        <span>www.clearpathcoaching.example.au</span>
      </li>
      <li>
        <span class="contact-icon"></span>
        <span>www.clearpathcoaching.example.au</span>
      </li>
    </ul>
  </section>
</body>
</html>
```